Need webdesign for service company that provides Car hiring service and transit service

We need a web design for a company that provides airport transit services and transport services including Limo, Corporate cars, Disability transit, Family transit service. We need is a simple and professional design.

Below is site which we like and also offer the same service http://www.ridelarkway.com.au/
Updates

Project Deadline Extended
Reason: Waiting for the Feedback from multiple stakeholders. Need the time to select and approve the design

Target Market(s)

Tourism, Travel

Industry/Entity Type

Airport

Number of Pages Required

3 page

Font styles to use
Decorative
Script

Requirements
Must have
• Simple and Professional, Site we like http://www.ridelarkway.com.au/ and also need to mobile friendly
Should not have
• Shouldn't have too many images

```html
<!DOCTYPE html>
<html lang="en">
<head>
<meta charset="utf-8">
<title>Ridewell – Private &amp; Business Transport</title>
<link href="https://fonts.googleapis.com/css2?family=Lato:wght@300;400;700;900&display=swap" rel="stylesheet">
<style>
:root{
  --ink:#333333;
  --ink-soft:#4a4a4a;
  --muted:#8a8a8a;
  --page:#f8f8f8;
  --white:#ffffff;
  --band:#ececec;
  --panel:#363636;
  --field-icon:#e9e9e9;
  --accent:#c98436;
  --rule:#dddddd;
}
*{box-sizing:border-box;margin:0;padding:0}
html,body{width:891px;height:1200px;overflow:hidden}
body{background:var(--page);font-family:'Lato',sans-serif;color:var(--ink);position:relative}

.site-header{position:absolute;left:0;top:0;width:891px;height:90px;background:var(--white)}
.brand{position:absolute;left:74px;top:30px;display:flex;align-items:center;gap:10px}
.brand-mark{width:16px;height:16px;border-radius:50%;background:var(--ink)}
.brand-name{font-size:26px;font-weight:400;letter-spacing:.5px;color:var(--ink)}
.header-icons{position:absolute;right:72px;top:38px;display:flex;gap:22px}
.header-icons svg{width:18px;height:18px;fill:var(--ink)}
.header-shadow{position:absolute;left:70px;top:88px;width:750px;height:12px;background:radial-gradient(ellipse at center top,rgba(0,0,0,.08),transparent 70%)}

.intro-title{position:absolute;top:142px;width:891px;text-align:center;font-size:32px;font-weight:700;letter-spacing:2.5px;color:var(--ink)}
.intro-sub{position:absolute;top:180px;width:891px;text-align:center;font-size:19px;font-weight:400;letter-spacing:2px;color:var(--ink-soft)}
.intro-text{position:absolute;left:74px;top:222px;width:730px;font-size:9px;line-height:17px;color:var(--ink);font-weight:400}

.quote-panel{position:absolute;left:74px;top:306px;width:273px;height:306px;background:var(--panel);padding:22px 13px}
.quote-title{color:var(--white);font-size:16px;letter-spacing:1.5px;font-weight:400;margin-bottom:15px}
.quote-title strong{font-weight:900}
.field{display:flex;height:29px;background:var(--white);margin-bottom:9px}
.field-icon{width:30px;background:var(--field-icon);display:flex;align-items:center;justify-content:center;border-right:1px solid #ccc}
.field-icon svg{width:9px;height:9px}
.field-input{flex:1;font-size:8px;color:#aaa;padding-left:7px;display:flex;align-items:center}
.quote-option{display:flex;align-items:center;color:var(--white);font-size:12px;letter-spacing:1.3px;height:30px;padding-left:10px;gap:14px}
.quote-option svg{width:10px;height:10px}
.estimate-btn{margin-top:12px;height:50px;background:var(--accent);color:var(--white);font-size:18px;font-weight:700;letter-spacing:2px;display:flex;align-items:center;justify-content:center}
.quote-note{margin-top:14px;font-size:8px;color:var(--muted);padding-left:10px}

.hero-slide{position:absolute;left:355px;top:306px;width:463px;height:306px;background:linear-gradient(180deg,#8a7a70 0%,#6e5a55 45%,#553f3d 100%)}
.hero-text{position:absolute;top:130px;width:100%;text-align:center;color:var(--white);font-size:21px;font-weight:300;line-height:24px}
.slider-dots{position:absolute;bottom:36px;width:100%;display:flex;justify-content:center;gap:9px}
.slider-dots span{width:10px;height:10px;border-radius:50%;background:var(--white)}
.slider-dots span.active{background:transparent;border:2px solid var(--white)}

.section-shadow{position:absolute;left:80px;top:650px;width:730px;height:20px;background:radial-gradient(ellipse at center,rgba(0,0,0,.07),transparent 70%)}

.services{position:absolute;left:0;top:729px;width:891px;height:362px;background:var(--band)}
.services-notch{position:absolute;left:418px;top:0;width:0;height:0;border-left:28px solid transparent;border-right:28px solid transparent;border-top:17px solid var(--page)}
.services-title{position:absolute;top:48px;width:891px;text-align:center;font-size:28px;font-weight:300;color:var(--ink)}
.service{position:absolute;top:112px;width:160px;text-align:center}
.service svg{width:108px;height:108px;display:block;margin:0 auto}
.service-name{margin-top:10px;font-size:15px;font-weight:300;letter-spacing:.4px;color:var(--ink)}
.service-desc{margin-top:6px;font-size:10px;line-height:15px;color:var(--ink-soft);font-weight:400}

.site-footer{position:absolute;left:0;top:1091px;width:891px;height:109px;background:var(--page)}
.footer-links{position:absolute;top:34px;width:891px;text-align:center;font-size:8px;color:var(--ink-soft)}
.footer-links span{margin:0 7px}
.footer-rule{position:absolute;left:74px;top:57px;width:744px;height:1px;background:var(--rule)}
.copyright{position:absolute;left:74px;top:75px;font-size:9px;color:var(--ink)}
.payments{position:absolute;right:73px;top:67px;display:flex;align-items:center;gap:18px;font-size:9px;color:var(--ink)}
.payments .pay-label{margin-right:-12px}
.pay-card{width:31px;height:20px;border-radius:2px}
.pay-1{background:#d9332b}.pay-2{background:#1a3f8f}.pay-3{background:#3a7fc4}.pay-4{background:#e07a2a}
</style>
</head>
<body>
<header class="site-header">
  <div class="brand"><span class="brand-mark"></span><span class="brand-name">RIDEWELL</span></div>
  <nav class="header-icons">
    <svg viewBox="0 0 18 18" aria-label="Menu"><rect x="1" y="3" width="16" height="2"/><rect x="1" y="7" width="16" height="2"/><rect x="1" y="11" width="16" height="2"/><rect x="1" y="15" width="16" height="2"/></svg>
    <svg viewBox="0 0 24 24" aria-label="Phone"><path d="M6.6 10.8a15 15 0 0 0 6.6 6.6l2.2-2.2c.3-.3.7-.4 1-.2 1.1.4 2.3.6 3.6.6.6 0 1 .4 1 1V20c0 .6-.4 1-1 1A17 17 0 0 1 3 4c0-.6.4-1 1-1h3.5c.6 0 1 .4 1 1 0 1.3.2 2.5.6 3.6.1.3 0 .7-.2 1z"/></svg>
    <svg viewBox="0 0 24 24" aria-label="Search"><path d="M10 3a7 7 0 0 1 5.6 11.2l5.1 5.1-1.4 1.4-5.1-5.1A7 7 0 1 1 10 3zm0 2.5a4.5 4.5 0 1 0 0 9 4.5 4.5 0 0 0 0-9z"/></svg>
  </nav>
</header>
<div class="header-shadow"></div>

<h1 class="intro-title">Private &amp; Business</h1>
<h2 class="intro-sub">Personalised Transport Service</h2>
<p class="intro-text">But I must explain to you how all this mistaken idea of denouncing pleasure and praising pain was born and I will give you a complete account of the system, and expound the actual teachings of the great explorer of the truth, the master-builder of human happiness. No one rejects, dislikes, or avoids pleasure itself, because it is pleasure, but because those who do not know how to pursue pleasure rationally encounter consequences that are extremely painful.</p>

<section class="quote-panel">
  <h3 class="quote-title"><strong>GET INSTANT</strong> QUOTE</h3>
  <div class="field"><div class="field-icon"><svg viewBox="0 0 10 10"><circle cx="5" cy="5" r="3.5" fill="none" stroke="#333" stroke-width="1.5"/></svg></div><div class="field-input">Origin ( Public Location or Exact Address )</div></div>
  <div class="field"><div class="field-icon"><svg viewBox="0 0 10 10"><path d="M5 0a3.5 3.5 0 0 1 3.5 3.5C8.5 6 5 10 5 10S1.5 6 1.5 3.5A3.5 3.5 0 0 1 5 0zm0 2.2a1.3 1.3 0 1 0 0 2.6 1.3 1.3 0 0 0 0-2.6z" fill="#333"/></svg></div><div class="field-input">Destination ( Public Location or Exact Address )</div></div>
  <div class="quote-option"><svg viewBox="0 0 10 10"><rect x="4" y="0" width="2" height="10" fill="#fff"/><rect x="0" y="4" width="10" height="2" fill="#fff"/></svg>ADD STOPS</div>
  <div class="quote-option"><svg viewBox="0 0 10 10"><circle cx="5" cy="5" r="4" fill="none" stroke="#fff" stroke-width="1.4"/><circle cx="5" cy="5" r="1.8" fill="#fff"/></svg>SHOW OTHER VEHICLES</div>
  <div class="estimate-btn">ESTIMATE FARE</div>
  <p class="quote-note">*See price guide for extras</p>
</section>

<section class="hero-slide" role="img" aria-label="Photo of an aircraft wing above the clouds">
  <p class="hero-text">WE PROVIDE AIRPORT TRANSIT SERVICES<br>AND TRANSPORT SERVICES</p>
  <div class="slider-dots"><span class="active"></span><span></span><span></span><span></span></div>
</section>

<div class="section-shadow"></div>

<section class="services">
  <div class="services-notch"></div>
  <h2 class="services-title">Our Services</h2>

  <article class="service" style="left:68px">
    <svg viewBox="0 0 108 108" fill="none" stroke="#666" stroke-width="1.6"><rect x="24" y="24" width="60" height="60" transform="rotate(45 54 54)"/><path d="M25 60v-6l4-2 6-5h36l6 5 6 1v7z"/><circle cx="33" cy="61" r="3.5"/><circle cx="75" cy="61" r="3.5"/><path d="M44 48v5M58 48v5"/></svg>
    <h3 class="service-name">LIMO SERVICES</h3>
    <p class="service-desc">Quis nostrud exercitation ullamco laboris nisi ut aliquip ex ea modo cillum dolore consequat.</p>
  </article>

  <article class="service" style="left:266px">
    <svg viewBox="0 0 108 108" fill="none" stroke="#666" stroke-width="1.6"><rect x="24" y="24" width="60" height="60" transform="rotate(45 54 54)"/><path d="M32 61v-7l4-1 5-7h22l6 7 6 1v7z"/><circle cx="40" cy="62" r="3.5"/><circle cx="68" cy="62" r="3.5"/><path d="M53 46v7"/></svg>
    <h3 class="service-name">CORPORATE CARS</h3>
    <p class="service-desc">Quis nostrud exercitation ullamco laboris nisi ut aliquip ex ea modo cillum dolore consequat.</p>
  </article>

  <article class="service" style="left:465px">
    <svg viewBox="0 0 108 108" fill="none" stroke="#666" stroke-width="1.6"><rect x="24" y="24" width="60" height="60" transform="rotate(45 54 54)"/><rect x="43" y="37" width="22" height="28" rx="3"/><path d="M46 42h16v9H46zM47 72l4-7M61 72l-4-7M40 72h28M48 34h12M54 34v3"/><circle cx="48" cy="59" r="1.2"/><circle cx="60" cy="59" r="1.2"/></svg>
    <h3 class="service-name">DISABILITY TRANSIT</h3>
    <p class="service-desc">Quis nostrud exercitation ullamco laboris nisi ut aliquip ex ea modo cillum dolore consequat.</p>
  </article>

  <article class="service" style="left:663px">
    <svg viewBox="0 0 108 108" fill="none" stroke="#666" stroke-width="1.6"><rect x="24" y="24" width="60" height="60" transform="rotate(45 54 54)"/><path d="M28 46h40l6 6 5 1v9H28z"/><path d="M32 50h8v5h-8zM43 50h8v5h-8zM54 50h8v5h-8z"/><circle cx="37" cy="62" r="3.2"/><circle cx="70" cy="62" r="3.2"/></svg>
    <h3 class="service-name">FAMILY TRANSIT</h3>
    <p class="service-desc">Quis nostrud exercitation ullamco laboris nisi ut aliquip ex ea modo cillum dolore consequat.</p>
  </article>
</section>

<footer class="site-footer">
  <nav class="footer-links"><span>Home</span>|<span>Sitemap</span>|<span>Privacy Policy</span>|<span>Terms &amp; Conditions</span></nav>
  <div class="footer-rule"></div>
  <p class="copyright">Copyrights © 2017 Ridewell - All Rights Reserved.</p>
  <div class="payments">
    <span class="pay-label">Our Payments:</span>
    <span class="pay-card pay-1"></span>
    <span class="pay-card pay-2"></span>
    <span class="pay-card pay-3"></span>
    <span class="pay-card pay-4"></span>
  </div>
</footer>
</body>
</html>
```